Business Card Design For Office Furniture Clearance Company

Kestrel Office Clearance - our company name pretty much explains what we do, we clear offices for high end clients, mainly plc's and large international companies.

We require a nice looking business card that displays professionalism but without being too serious.

It would be nice to see just a little more than a conventional boring business card, make sure you add some flare.

Industry/Entity Type

Office Furniture

Contact Information for Business Card

CARD 1

Mark Holloway
Director
mark@kestrelofficeclearance.co.uk
m: 07700 153928

t: 01632 960418
www.kestrelofficeclearance.co.uk

Kestrel Office Clearance
Unit K4 B
2-8 Fenwick Lane
Ashcombe
Westbridge
ZZ9 4QT

office clearances at no cost… hard to beat a deal like that.

CARD 2

Peter Radford
Director
peter@kestrelofficeclearance.co.uk
m: 07700 382615

t: 01632 960418

Kestrel Office Clearance
Unit K4 B
2-8 Fenwick Lane
Ashcombe
Westbridge
ZZ9 4QT

Font styles to use
Sans Serif

Requirements
Must have
• A white background - as we have a blue logo.
Nice to have
• Nice use of the logo - play around with this and dissect it.

```html
<!DOCTYPE html>
<html lang="en">
<head>
<meta charset="utf-8">
<title>Kestrel Office Clearance – Business Card</title>
<link rel="stylesheet" href="https://fonts.googleapis.com/css2?family=Arimo:wght@400;700&display=swap">
<style>
  :root {
    --blue: #1f7fc4;
    --blue-deep: #1668a3;
    --ink: #2b2b2b;
    --grey-text: #555558;
    --rule: #1e1e1e;
    --bar-grey: #4a4a4d;
    --backdrop: #e9e9eb;
    --card-white: #ffffff;
    --dark-card: #3b3b3e;
    --dark-card-edge: #2a2a2c;
    --soft-light: #c9c9cc;
  }
  * { box-sizing: border-box; margin: 0; padding: 0; }
  html, body {
    width: 1200px; height: 950px; overflow: hidden;
    background: var(--backdrop);
    font-family: "Arimo", Arial, sans-serif;
  }
  .stage {
    width: 1200px; height: 950px;
    display: flex; flex-direction: column; align-items: center; justify-content: center;
    gap: 36px;
  }
  .card {
    position: relative; width: 760px; height: 434px; overflow: hidden;
    box-shadow: 0 10px 30px rgba(0,0,0,.18);
  }

  /* Back of card */
  .card--back {
    background: linear-gradient(135deg, var(--dark-card) 0%, var(--dark-card-edge) 100%);
  }
  .back-sheen {
    position: absolute; top: 0; left: 560px; width: 70px; height: 100%;
    background: linear-gradient(90deg, rgba(255,255,255,0) 0%, rgba(255,255,255,.12) 50%, rgba(255,255,255,0) 100%);
  }
  .back-mark {
    position: absolute; top: 110px; left: 230px;
    display: flex; align-items: center; gap: 22px;
  }
  .back-mark__circle {
    width: 150px; height: 150px; border-radius: 50%;
    background: var(--card-white);
  }
  .back-mark__name {
    color: var(--soft-light); font-size: 24px; font-weight: 700; line-height: 1.2;
  }
  .tagline {
    position: absolute; right: 40px; top: 318px;
    color: var(--soft-light); font-size: 16px;
  }

  /* Front of card */
  .card--front { background: var(--card-white); }
  .front-mark {
    position: absolute; top: 62px; right: 50px;
    display: flex; align-items: center; gap: 18px;
  }
  .front-mark__name {
    color: var(--blue); font-size: 18px; font-weight: 700; text-align: right; line-height: 1.25;
  }
  .front-mark__circle {
    width: 132px; height: 132px; border-radius: 50%;
    background: radial-gradient(circle at 35% 35%, #3b9ad9 0%, var(--blue) 55%, var(--blue-deep) 100%);
  }
  .person { position: absolute; left: 50px; top: 150px; }
  .person__name { color: var(--blue); font-size: 23px; font-weight: 700; }
  .person__role { color: var(--ink); font-size: 15px; margin-top: 4px; }
  .divider {
    position: absolute; left: 50px; right: 40px; top: 214px;
    height: 1px; background: var(--rule);
  }
  .contacts { position: absolute; left: 50px; top: 232px; list-style: none; }
  .contacts li {
    display: flex; align-items: center; gap: 8px;
    color: var(--grey-text); font-size: 16px; line-height: 25px;
  }
  .contacts svg { width: 15px; height: 15px; fill: var(--ink); flex: none; }
  .address {
    position: absolute; right: 40px; top: 234px;
    text-align: right; font-style: normal; color: var(--grey-text); font-size: 16px; line-height: 22px;
  }
  .address__company { color: var(--blue); font-weight: 700; font-size: 17px; }
  .front-bars { position: absolute; left: 0; bottom: 0; width: 760px; height: 22px; }
</style>
</head>
<body>
<main class="stage">

  <section class="card card--back" aria-label="Card back">
    <div class="back-sheen" role="img" aria-label="Textured light strip"></div>
    <div class="back-mark">
      <div class="back-mark__circle"></div>
      <div class="back-mark__name">Kestrel<br>Office Clearance</div>
    </div>
    <p class="tagline">office clearances at no cost… hard to beat a deal like that.</p>
  </section>

  <section class="card card--front" aria-label="Card front">
    <div class="front-mark">
      <div class="front-mark__name">Kestrel<br>Office Clearance</div>
      <div class="front-mark__circle"></div>
    </div>

    <div class="person">
      <h1 class="person__name">Mark Holloway</h1>
      <p class="person__role">Director</p>
    </div>
    <div class="divider"></div>

    <ul class="contacts">
      <li>
        <svg viewBox="0 0 16 16" aria-hidden="true"><path d="M3.6 1.2l2.3 2.6-1.3 2.1c.9 1.9 2.6 3.6 4.5 4.5l2.1-1.3 2.6 2.3-1.3 2.4c-5.6.2-10.6-4.8-10.4-10.4z"/></svg>
        01632 960418
      </li>
      <li>
        <svg viewBox="0 0 16 16" aria-hidden="true"><path d="M4.5 0h7c.8 0 1.5.7 1.5 1.5v13c0 .8-.7 1.5-1.5 1.5h-7C3.7 16 3 15.3 3 14.5v-13C3 .7 3.7 0 4.5 0zM5 2v10h6V2zm3 11a1 1 0 100 2 1 1 0 000-2z"/></svg>
        07700 153928
      </li>
      <li>
        <svg viewBox="0 0 16 16" aria-hidden="true"><path d="M1 3h14v1.2L8 9 1 4.2zm0 2.6l7 4.8 7-4.8V13H1z"/></svg>
        mark@kestrelofficeclearance.co.uk
      </li>
      <li>
        <svg viewBox="0 0 16 16" aria-hidden="true"><path d="M8 1a7 7 0 100 14A7 7 0 008 1zm0 1.5c.9 1 1.6 2.5 1.8 4.5H6.2C6.4 5 7.1 3.5 8 2.5zM2.6 9h3.6c.2 1.8.8 3.3 1.8 4.5A5.5 5.5 0 012.6 9zm7.2 0h3.6A5.5 5.5 0 018 13.5c1-1.2 1.6-2.7 1.8-4.5z"/></svg>
        www.kestrelofficeclearance.co.uk
      </li>
    </ul>

    <address class="address">
      <div class="address__company">Kestrel Office Clearance</div>
      Unit K4 B, 2-8 Fenwick Lane<br>
      Ashcombe, Westbridge<br>
      ZZ9 4QT
    </address>

    <svg class="front-bars" viewBox="0 0 760 22" aria-hidden="true">
      <polygon points="0,10 400,10 392,22 0,22" fill="var(--blue)"/>
      <polygon points="404,0 760,0 760,22 394,22" fill="var(--bar-grey)"/>
    </svg>
  </section>

</main>
</body>
</html>
```